Fernhale Business Card Design

We are looking for a fresh business card design for our new logo. We would like a business card that is unique but friendly. We are in the window coverings business offering blinds, shutters and shades for homes.

Target Market(s)

Targeting the end-consumer

Industry/Entity Type

Business

Requirements
Must have
• Must have a dedicates space for a photo of our sales person. Must contain our new logo (attached).

```html
<!DOCTYPE html>
<html lang="en">
<head>
<meta charset="utf-8">
<title>Fernhale Business Card</title>
<link rel="stylesheet" href="https://fonts.googleapis.com/css2?family=Open+Sans:wght@400;600;700&display=swap">
<style>
  :root {
    --stage: #e9eaec;
    --card: #fbfbfb;
    --ink: #2f2f2f;
    --ink-soft: #3c3c3c;
    --green: #5f9f22;
    --green-deep: #4c8a17;
    --charcoal: #3a3b3d;
    --rule: #a9a9a9;
  }
  * { margin: 0; padding: 0; box-sizing: border-box; }
  html, body { width: 1200px; height: 970px; overflow: hidden; }
  body {
    background: var(--stage);
    font-family: "Open Sans", Arial, sans-serif;
    color: var(--ink);
    position: relative;
  }
  .card {
    position: absolute;
    left: 100px; top: 207px;
    width: 1000px; height: 556px;
    background: var(--card);
    box-shadow: 0 10px 30px rgba(0,0,0,0.12);
    overflow: hidden;
  }
  .brand {
    position: absolute;
    left: 50px; top: 86px;
    display: flex; align-items: center; gap: 26px;
  }
  .brand-mark {
    width: 60px; height: 60px;
    background: var(--green);
  }
  .brand-name {
    font-size: 66px; font-weight: 400;
    color: var(--ink-soft);
    line-height: 1;
  }
  .portrait {
    position: absolute;
    left: 807px; top: 102px;
    width: 146px; height: 133px;
    border: 6px solid var(--green);
    border-radius: 22px 4px 22px 4px;
    background: linear-gradient(180deg, #8c8d8f 0%, #a3a29f 55%, #6f8a3c 100%);
  }
  .person {
    position: absolute;
    right: 47px; top: 254px;
    text-align: right;
  }
  .person-name {
    font-size: 29px; font-weight: 700;
    color: var(--green);
    letter-spacing: 0.5px;
    line-height: 1.2;
  }
  .person-role {
    font-size: 22px; font-weight: 400;
    color: var(--ink);
    line-height: 1.2;
  }
  .divider {
    position: absolute;
    top: 339px; height: 2px;
  }
  .divider--grey { left: 48px; width: 617px; background: var(--rule); }
  .divider--green { left: 665px; width: 288px; background: var(--green); }
  .contacts {
    position: absolute;
    left: 50px; top: 360px;
    list-style: none;
  }
  .contacts li {
    display: flex; align-items: center; gap: 10px;
    font-size: 23px; height: 34px;
    color: var(--ink);
  }
  .contacts svg { width: 22px; height: 22px; fill: var(--green); flex: none; }
  .address {
    position: absolute;
    right: 47px; top: 410px;
    text-align: right;
    font-size: 23px; line-height: 29px;
    color: var(--ink);
  }
  .footer-band {
    position: absolute;
    left: 0; bottom: 0;
    width: 1000px; height: 40px;
  }
</style>
</head>
<body>
  <div class="card">
    <div class="brand">
      <div class="brand-mark"></div>
      <div class="brand-name">Fernhale</div>
    </div>

    <div class="portrait" role="img" aria-label="Photo of the sales person"></div>

    <div class="person">
      <div class="person-name">MAREN HOLLOWAY</div>
      <div class="person-role">Managing Director</div>
    </div>

    <div class="divider divider--grey"></div>
    <div class="divider divider--green"></div>

    <ul class="contacts">
      <li>
        <svg viewBox="0 0 24 24" aria-hidden="true"><path d="M8 2h8a2 2 0 0 1 2 2v16a2 2 0 0 1-2 2H8a2 2 0 0 1-2-2V4a2 2 0 0 1 2-2zm0 3v11h8V5zm4 13a1.3 1.3 0 1 0 0 2.6A1.3 1.3 0 0 0 12 18z"/></svg>
        + 000 000 0000
      </li>
      <li>
        <svg viewBox="0 0 24 24" aria-hidden="true"><path d="M2 9c0-2 4-4 10-4s10 2 10 4v2h-5V9c-1-.6-3-1-5-1s-4 .4-5 1v2H2zm5 3h10l3 8H4z"/></svg>
        + 000 000 0000
      </li>
      <li>
        <svg viewBox="0 0 24 24" aria-hidden="true"><path d="M2 5h20v14H2zm2 2v.5l8 5.5 8-5.5V7zm0 3v7h16v-7l-8 5.5z"/></svg>
        elliot@fernhale.com
      </li>
      <li>
        <svg viewBox="0 0 24 24" aria-hidden="true"><path d="M12 2a10 10 0 1 0 0 20 10 10 0 0 0 0-20zm0 2c1.4 1.6 2.3 4 2.5 7h-5C9.7 8 10.6 5.6 12 4zm-7.9 7a8 8 0 0 1 5.4-6.6C8.5 6.2 7.6 8.5 7.5 11zm0 2h3.4c.1 2.5 1 4.8 2 6.6A8 8 0 0 1 4.1 13zm5.4 0h5c-.2 3-1.1 5.4-2.5 7-1.4-1.6-2.3-4-2.5-7zm7 0h3.4a8 8 0 0 1-5.4 6.6c1-1.8 1.9-4.1 2-6.6zm0-2c-.1-2.5-1-4.8-2-6.6a8 8 0 0 1 5.4 6.6z"/></svg>
        www.fernhale.com
      </li>
    </ul>

    <div class="address">
      Level 14, 8 Harbour Point<br>
      Sydney, 20, New South Wales
    </div>

    <svg class="footer-band" viewBox="0 0 1000 40" preserveAspectRatio="none" aria-hidden="true">
      <polygon points="0,15 500,15 478,40 0,40" fill="var(--green)"/>
      <polygon points="530,0 1000,0 1000,40 496,40" fill="var(--charcoal)"/>
    </svg>
  </div>
</body>
</html>
```